American cannabis tech company business card design

Pavrel.com is seeking a modern, professional, and brand-aligned business card that represents our company and its core values: Mission, Story, Values, and Impact. As an innovative cannabis company, we want a business card that is not only visually appealing but also serves as a representation of who we are and what we stand for.

Project Scope: Design a double-sided business card that integrates our brand identity and core values. Incorporate our key brand elements, ensuring a sleek and contemporary aesthetic. Visually reflect our core values (Mission, Story, Values, Impact) in a way that is engaging yet professional.

Target Market(s)

Vendors, third parties,

Contact Information for Business Card

Contact details (name, title, email, phone, website, etc.)

Font styles to use
Other font styles liked:
• Caslon, Centra

Colors

Designer to choose colors to be used in the design.

Requirements
Must have
• Pavrel.com logo and branding A creative yet clean way to integrate our core values (Mission, Story, Values, Impact) Modern typography and a well-structured layout
Nice to have
• forest green, grey, white, black
Should not have
• references to marijuana, leafs, plants, or related product

```html
<!DOCTYPE html>
<html lang="en">
<head>
<meta charset="utf-8">
<title>Pavrel.com Business Card</title>
<link rel="stylesheet" href="https://fonts.googleapis.com/css2?family=Libre+Caslon+Text:wght@400;700&display=swap">
<style>
  :root {
    --forest: #132b17;
    --paper: #f2f2f2;
    --paper-ink: #e4e4e2;
    --paper-muted: #9fb0a2;
    --text-grey: #3a3a3a;
    --backdrop: #d8dcda;
  }
  * { margin: 0; padding: 0; box-sizing: border-box; }
  html, body {
    width: 1200px; height: 1200px; overflow: hidden;
    background: var(--backdrop);
    font-family: "Libre Caslon Text", Georgia, serif;
  }
  .card {
    position: absolute; left: 255px;
    width: 729px; height: 416px;
    border-radius: 4px;
  }
  .card--front { top: 134px; background: var(--paper); color: var(--forest); }
  .card--back {
    top: 611px; background: var(--forest);
    display: flex; flex-direction: column; align-items: center; justify-content: center;
  }
  .wordmark { font-weight: 700; letter-spacing: 0.01em; line-height: 1; }
  .card--front .wordmark {
    position: absolute; top: 52px; right: 63px; font-size: 54px;
  }
  .card--back .wordmark {
    font-size: 112px; color: var(--paper-ink); margin-top: 10px;
  }
  .values {
    position: absolute; left: 0; right: 0; bottom: 34px;
    display: flex; justify-content: center; gap: 18px;
    list-style: none;
    font-size: 12px; letter-spacing: 0.28em; text-transform: uppercase;
    color: var(--paper-muted);
  }
  .values__item + .values__item::before {
    content: "·"; margin-right: 18px; letter-spacing: 0;
  }
  .person { position: absolute; left: 64px; top: 200px; }
  .person__name { font-size: 23px; font-weight: 700; letter-spacing: 0.01em; line-height: 1.2; }
  .person__title { font-size: 17px; color: var(--text-grey); margin-top: 2px; }
  .contact { position: absolute; left: 64px; top: 276px; list-style: none; }
  .contact__item {
    display: flex; align-items: center; gap: 10px;
    font-size: 17px; color: var(--text-grey); height: 27.5px;
  }
  .contact__icon { width: 15px; height: 15px; fill: var(--forest); flex: none; }
</style>
</head>
<body>
  <section class="card card--front">
    <div class="wordmark">PAVREL</div>
    <div class="person">
      <div class="person__name">OWEN HARLOW</div>
      <div class="person__title">Owner</div>
    </div>
    <ul class="contact">
      <li class="contact__item">
        <svg class="contact__icon" viewBox="0 0 16 16" aria-hidden="true"><path d="M3.5 1.5l2.5 3-1.5 1.8c.8 1.8 2.3 3.3 4.2 4.2l1.8-1.5 3 2.5-1.5 2.5C7 13.5 2.5 9 1 3z"/></svg>
        <span>+1 405-555-0148</span>
      </li>
      <li class="contact__item">
        <svg class="contact__icon" viewBox="0 0 16 16" aria-hidden="true"><path d="M1 3h14v2L8 9 1 5z"/><path d="M1 6.5l7 4 7-4V13H1z"/></svg>
        <span>team@pavrel.com</span>
      </li>
      <li class="contact__item">
        <svg class="contact__icon" viewBox="0 0 16 16" aria-hidden="true"><circle cx="8" cy="8" r="7"/><path d="M4 4.5c1.5.2 2.5 1.2 2 2.5-.4 1-1.8 1-1.5 2.5.2 1 1 1.5 1 3M10 2.5c-.5 1.3.5 2 1.5 2.2 1 .2 1.5 1.3.8 2.3-.6.9-1.8.6-2.2 1.8-.3 1 .5 2 1.5 2.5" fill="none" stroke="var(--paper)" stroke-width="1.2"/></svg>
        <span>www.pavrel.com</span>
      </li>
    </ul>
  </section>

  <section class="card card--back">
    <div class="wordmark">PAVREL</div>
    <ul class="values">
      <li class="values__item">Mission</li>
      <li class="values__item">Story</li>
      <li class="values__item">Values</li>
      <li class="values__item">Impact</li>
    </ul>
  </section>
</body>
</html>
```